Kelvaro.ch is looking for business card letterhead and envelope C5 with WOW effect

We need a strong business card for our company Kelvaro.ch, logo is available. You want a black or dark background on which the logo Stark r% 26 # 252; appears. Letterhead and envelope in C5 format should be in a similar design, but does not have to be We need a strong business card for our company Kelvaro.ch, logo is available. A black or dark background is desired, on which the logo Stark comes across. The letterhead and the envelope in C5 format should have a similar design.

Target Market(s)

Private customers as well as entrepreneurs

Contact Information for Business Card

E-mail: info@kelvaro-example.ch
Web.www.Kelvaro-example.ch
Tel: +41 ( 0 ) 79 482 6037
Adresse:
Lindenweg 14
9406 Tarnbach

Hier kann man Icons verwenden für Email,Tel und Adressse

Font styles to use
Other font styles liked:
• Dubai,bold

Colors

Designer to choose colors to be used in the design.

Requirements
Must have
• WOW effect
Nice to have
• R% 26 # 252; back business card with our service listings. - VEHICLE LABELING - SHOP WINDOW LABELING - STICKERS AND MUCH MORE ... in red color

```html
<!DOCTYPE html>
<html lang="de">
<head>
<meta charset="utf-8">
<title>Kelvaro.ch – Visitenkarte</title>
<link href="https://fonts.googleapis.com/css2?family=Ubuntu:wght@400;500;700&display=swap" rel="stylesheet">
<style>
  :root {
    --backdrop: #4a423b;
    --card: #1c1c1d;
    --card-light: #2b2b2c;
    --yellow: #fdd22c;
    --gold: #b8962a;
    --white: #f4f4f4;
    --red: #e0141e;
  }
  * { box-sizing: border-box; margin: 0; padding: 0; }
  html, body {
    width: 1200px; height: 930px; overflow: hidden;
    background: var(--backdrop);
    font-family: "Ubuntu", sans-serif;
  }
  .stage { position: relative; width: 1200px; height: 930px; }
  .card {
    position: absolute;
    width: 540px; height: 340px;
    border-radius: 22px;
    background: linear-gradient(115deg, var(--card) 0%, var(--card-light) 45%, var(--card) 100%);
    box-shadow: 0 14px 30px rgba(0,0,0,.45);
    overflow: hidden;
  }
  .card--front { left: 80px; top: 90px; }
  .card--back { left: 580px; top: 500px; }

  .pattern-area {
    position: absolute;
    border-radius: 14px;
    background: radial-gradient(circle at 40% 45%, #ffd83a 0%, #f2c21c 55%, rgba(242,194,28,.0) 100%);
  }
  .card--front .pattern-area { left: 50px; top: 95px; width: 170px; height: 150px; }
  .card--back .pattern-area { left: 45px; top: 140px; width: 220px; height: 175px; }

  .brand {
    position: absolute; left: 240px; top: 110px;
    display: flex; align-items: center; gap: 10px;
  }
  .brand__name {
    font-weight: 700; font-size: 38px; letter-spacing: 1px;
    color: var(--white); text-transform: uppercase;
  }
  .brand__dot { width: 10px; height: 10px; background: var(--yellow); border-radius: 50%; }

  .services {
    position: absolute; right: 40px; top: 170px;
    list-style: none; text-align: right;
  }
  .services li {
    color: var(--white); font-size: 14px; line-height: 20px;
    text-transform: uppercase; letter-spacing: .2px;
  }
  .services li::after {
    content: ""; display: inline-block;
    width: 7px; height: 7px; margin-left: 8px;
    border: 2px solid var(--red); border-radius: 50%;
    vertical-align: middle;
  }

  .person { position: absolute; left: 290px; top: 50px; }
  .person__name {
    font-weight: 700; font-size: 26px; letter-spacing: 2px;
    color: var(--white); text-transform: uppercase;
  }
  .person__name .surname { color: var(--yellow); }
  .person__role { color: var(--white); font-size: 14px; margin-top: 2px; padding-left: 18px; }
  .divider {
    position: absolute; left: 300px; top: 126px; width: 210px; height: 1px;
    background: linear-gradient(90deg, var(--gold), rgba(184,150,42,.2));
  }
  .contact { position: absolute; left: 305px; top: 142px; list-style: none; }
  .contact li {
    display: flex; align-items: center; gap: 10px;
    color: var(--white); font-size: 14px; line-height: 24px; white-space: nowrap;
  }
  .contact svg { width: 13px; height: 13px; flex: none; }
</style>
</head>
<body>
<main class="stage">

  <section class="card card--front" aria-label="Vorderseite">
    <div class="pattern-area" role="img" aria-label="Gelbes Wabenmuster als Dekoration"></div>
    <div class="brand">
      <span class="brand__name">Kelvaro.ch</span>
      <span class="brand__dot"></span>
    </div>
    <ul class="services">
      <li>Vehicle labeling</li>
      <li>Shop window labeling</li>
      <li>Stickers and much more</li>
    </ul>
  </section>

  <section class="card card--back" aria-label="Rückseite">
    <div class="pattern-area" role="img" aria-label="Gelbes Wabenmuster als Dekoration"></div>
    <div class="person">
      <p class="person__name">Jonas <span class="surname">Brunner</span></p>
      <p class="person__role">Director</p>
    </div>
    <div class="divider"></div>
    <ul class="contact">
      <li>
        <svg viewBox="0 0 16 16" aria-hidden="true"><path fill="#fdd22c" d="M3.6 1.5l2.3 2.6-1.3 1.9c.9 2 2.5 3.6 4.5 4.5l1.9-1.3 2.6 2.3-1.4 2.2C7 13.5 2.5 9 1.3 2.9z"/></svg>
        +41 ( 0 ) 79 482 6037
      </li>
      <li>
        <svg viewBox="0 0 16 16" aria-hidden="true"><rect x="1.5" y="3.5" width="13" height="9" rx="1" fill="none" stroke="#fdd22c" stroke-width="1.6"/><path d="M2 4l6 5 6-5" fill="none" stroke="#fdd22c" stroke-width="1.6"/></svg>
        info@kelvaro-example.ch
      </li>
      <li>
        <svg viewBox="0 0 16 16" aria-hidden="true"><g fill="none" stroke="#fdd22c" stroke-width="1.4"><circle cx="8" cy="8" r="6.3"/><ellipse cx="8" cy="8" rx="2.8" ry="6.3"/><path d="M1.7 8h12.6M2.8 4.8h10.4M2.8 11.2h10.4"/></g></svg>
        www.Kelvaro-example.ch
      </li>
      <li>
        <svg viewBox="0 0 16 16" aria-hidden="true"><path fill="#fdd22c" d="M8 1a5 5 0 0 0-5 5c0 3.8 5 9 5 9s5-5.2 5-9a5 5 0 0 0-5-5zm0 7a2 2 0 1 1 0-4 2 2 0 0 1 0 4z"/></svg>
        Lindenweg 14 9406 Tarnbach
      </li>
    </ul>
  </section>

</main>
</body>
</html>
```